New Food Retail Product: 100% Quinoa Pasta

Do you enjoy eating food?

We need a packaging design completed for a new product which is a 100% Quinoa Pasta originating from Peru in Latin American. I currently do not have a name for this product and I am open to suggestions. For pasta design ideas please search "pasta packaging designs" in mosaiqo for ideas.My product is Gluteen free, has a high level of protein and does not contain any GMOs - the package design needs to fit 8oz or 227grams of pasta. As per the colours and design I am open to your ideas as I will know the one once it has been created for me.

Target Market(s)

Diabetes, Athletes, Millennials, Generation X, Individuals will high blood pressure
Gluten Free dieters, Vegans

Industry/Entity Type

Retail

Font styles to use
Sans Serif

Colors
33b8a4
3277b5
acd036
fbee3e
ec1f27

Requirements
Must have
• Clean upscale design as the product is a premium priced product
• For this project the designs required are for the following types of pasta: Fusilli and Linguine. As far as a picture the product looks lIke brown while wheat pasta.

```html
<!DOCTYPE html>
<html lang="en">
<head>
<meta charset="utf-8">
<title>Andelia Pasta – Quinoa Fusilli Packaging</title>
<link href="https://fonts.googleapis.com/css2?family=Arimo:wght@400;700&display=swap" rel="stylesheet">
<style>
  :root {
    --page: #ffffff;
    --brand-orange: #f5a320;
    --box-front: #efe6c4;
    --box-side: #e3d8ac;
    --ink: #1d1a16;
    --gold: #a88d50;
    --gold-ring: #c9b37a;
    --pasta-light: #f2c96a;
    --pasta-mid: #dfa93a;
    --pasta-dark: #b98524;
  }
  * { box-sizing: border-box; margin: 0; padding: 0; }
  html, body { width: 1200px; height: 1140px; overflow: hidden; background: var(--page); }
  body { position: relative; font-family: "Arimo", Arial, sans-serif; color: var(--ink); }

  .brand-lockup { position: absolute; left: 360px; top: 120px; width: 340px; text-align: center; color: var(--brand-orange); }
  .brand-lockup .name { font-size: 84px; font-weight: 400; line-height: 1; letter-spacing: 1px; }
  .brand-lockup .sub { margin-top: 14px; font-size: 22px; font-weight: 400; letter-spacing: 22px; padding-left: 22px; }

  .package { position: absolute; top: 380px; height: 680px; display: flex; }
  .package--nutrition { left: 170px; }
  .package--brand { left: 660px; }

  .panel-side { width: 130px; height: 100%; background: var(--box-side); position: relative; }
  .panel-front { width: 280px; height: 100%; background: var(--box-front); position: relative; }

  .front-logo { position: absolute; left: 22px; top: 70px; }
  .front-logo .name { font-size: 46px; font-weight: 400; line-height: 1; }
  .front-logo .sub { font-size: 14px; font-weight: 700; letter-spacing: 13px; margin-top: 8px; }
  .front-details { position: absolute; left: 22px; top: 170px; width: 130px; text-align: right; font-size: 11px; line-height: 1.5; }
  .front-details .weight { font-size: 14px; }
  .front-details .origin { font-size: 8px; }

  .pasta-window { position: absolute; left: 0; top: 0; }

  .quinoa-badge { position: absolute; left: 158px; top: 506px; width: 116px; height: 116px; border-radius: 50%;
    background: var(--gold); border: 2px solid var(--gold-ring); box-shadow: inset 0 0 0 12px var(--gold), inset 0 0 0 13px var(--gold-ring);
    display: flex; align-items: center; justify-content: center; text-align: center; color: #fff; font-weight: 700; font-size: 15px; line-height: 1.3; }

  .side-logo { padding: 18px 10px 0; }
  .side-logo .name { font-size: 24px; line-height: 1; }
  .side-logo .sub { font-size: 9px; font-weight: 700; letter-spacing: 6px; margin-top: 4px; }

  .nutrition-table { margin: 12px 8px 0; border: 2px solid var(--ink); background: #fff; padding: 4px; font-size: 8px; line-height: 1.6; }
  .nutrition-table h3 { font-size: 14px; font-weight: 700; border-bottom: 4px solid var(--ink); padding-bottom: 2px; margin-bottom: 2px; }
  .nutrition-table .row { display: flex; justify-content: space-between; border-bottom: 1px solid var(--ink); }
  .nutrition-table .row:last-child { border-bottom: none; }

  .side-copy { margin: 18px 10px 0; font-size: 10px; line-height: 1.55; }

  .side-vertical { position: absolute; left: 50%; bottom: 30px; transform-origin: left bottom; transform: translateX(42px) rotate(-90deg); white-space: nowrap; }
  .side-vertical .name { font-size: 62px; line-height: 1; }
  .side-vertical .sub { font-size: 18px; font-weight: 700; letter-spacing: 18px; margin-top: 2px; }
</style>
</head>
<body>

<header class="brand-lockup">
  <div class="name">Andelia</div>
  <div class="sub">PASTA</div>
</header>

<section class="package package--nutrition">
  <div class="panel-side">
    <div class="side-logo">
      <div class="name">Andelia</div>
      <div class="sub">PASTA</div>
    </div>
    <div class="nutrition-table">
      <h3>Nutrition Facts</h3>
      <div class="row"><span>Serving Size</span><span>56g</span></div>
      <div class="row"><span>Servings</span><span>4</span></div>
      <div class="row"><span>Calories</span><span>200</span></div>
      <div class="row"><span>Total Fat</span><span>1g</span></div>
      <div class="row"><span>Sodium</span><span>0mg</span></div>
      <div class="row"><span>Carbs</span><span>41g</span></div>
      <div class="row"><span>Fiber</span><span>3g</span></div>
      <div class="row"><span>Sugars</span><span>1g</span></div>
      <div class="row"><span>Protein</span><span>8g</span></div>
    </div>
    <p class="side-copy">Pure Peruvian quinoa flour, gluten free and high in protein. Boil in salted water eight minutes, drain and serve.</p>
  </div>
  <div class="panel-front">
    <svg class="pasta-window" width="280" height="680" viewBox="0 0 280 680" role="img" aria-label="Window showing golden fusilli pasta">
      <defs>
        <linearGradient id="pasta-fill-a" x1="0" y1="0" x2="1" y2="1">
          <stop offset="0" stop-color="var(--pasta-light)"/>
          <stop offset="0.5" stop-color="var(--pasta-mid)"/>
          <stop offset="1" stop-color="var(--pasta-dark)"/>
        </linearGradient>
      </defs>
      <polygon points="162,34 272,34 126,612 17,612" fill="url(#pasta-fill-a)"/>
    </svg>
    <div class="front-logo">
      <div class="name">Andelia</div>
      <div class="sub">PASTA</div>
    </div>
    <div class="front-details">
      <div class="weight">227g</div>
      <div>Fusilli (Little Springs)</div>
      <div class="origin">Product of Canada</div>
    </div>
    <div class="quinoa-badge">100%<br>Quinoa<br>Pasta</div>
  </div>
</section>

<section class="package package--brand">
  <div class="panel-side">
    <div class="side-vertical">
      <div class="name">Andelia</div>
      <div class="sub">PASTA</div>
    </div>
  </div>
  <div class="panel-front">
    <svg class="pasta-window" width="280" height="680" viewBox="0 0 280 680" role="img" aria-label="Window showing golden fusilli pasta">
      <defs>
        <linearGradient id="pasta-fill-b" x1="0" y1="0" x2="1" y2="1">
          <stop offset="0" stop-color="var(--pasta-light)"/>
          <stop offset="0.5" stop-color="var(--pasta-mid)"/>
          <stop offset="1" stop-color="var(--pasta-dark)"/>
        </linearGradient>
      </defs>
      <polygon points="162,34 272,34 126,612 17,612" fill="url(#pasta-fill-b)"/>
    </svg>
    <div class="front-logo">
      <div class="name">Andelia</div>
      <div class="sub">PASTA</div>
    </div>
    <div class="front-details">
      <div class="weight">227g</div>
      <div>Fusilli (Little Springs)</div>
      <div class="origin">Product of Canada</div>
    </div>
    <div class="quinoa-badge">100%<br>Quinoa<br>Pasta</div>
  </div>
</section>

</body>
</html>
```